Lifecoach needs website design based on a standard Wordpress theme

I need a website for my new lifecoaching business that can be easily implemented in Wordpress, it needs to be compatible with a standard Wordpress theme. So I can place the pictures, texts etc. in a standard theme of Wordpress.

I want the design to be a very good feeling and playfull one, based on my logo.

Target Market(s)

I will coach people to reach their goals and dreams in life.

Industry/Entity Type

Business

Requirements
Must have
• Can be easy implemented in Wordpress.
Nice to have
• Photo's of nature are nice.

```html
<!DOCTYPE html>
<html lang="en">
<head>
<meta charset="utf-8">
<title>Ruben ter Horst Lifecoach</title>
<link rel="stylesheet" href="https://fonts.googleapis.com/css2?family=Source+Sans+3:ital,wght@0,400;0,600;1,600&family=Kaushan+Script&display=swap">
<style>
:root{
  --brand:#0b4a7e;
  --brand-dark:#0a4577;
  --ink:#111;
  --text:#3d3d3d;
  --panel:#f0f0f0;
  --frame:#ffffff;
  --rule:#dcdcdc;
  --white:#fff;
  --button:#5d5d5d;
}
*{margin:0;padding:0;box-sizing:border-box}
html,body{width:1100px;height:1200px;overflow:hidden;background:#fff}
body{position:relative;font-family:"Source Sans 3",Arial,sans-serif;color:var(--text)}
.abs{position:absolute}

.brand{left:98px;top:14px;display:flex;align-items:center;gap:10px}
.brand-mark{width:56px;height:56px;border-radius:50%;border:3px solid var(--brand)}
.brand-name{color:var(--brand);font-size:21px;font-weight:400;line-height:1.1}

.nav{top:27px;left:452px;display:flex;gap:0;font-size:15px;color:#333}
.nav a{display:block;height:32px;line-height:32px;padding:0 9px;color:#333;text-decoration:none;margin-right:19px}
.nav a.active{background:var(--brand);color:var(--white);margin-right:18px}

.frame{background:var(--frame);box-shadow:0 0 3px rgba(0,0,0,.3);padding:5px}
.hero{left:91px;top:94px;width:920px;height:341px}
.hero-photo{width:100%;height:100%;position:relative;
  background:linear-gradient(180deg,#cfdbe6 0%,#7f9bb4 18%,#4c6f5a 40%,#2f6a3a 60%,#3f8a2a 78%,#4f9a1e 100%)}
.hero-caption{position:absolute;left:0;right:0;bottom:0;height:60px;background:rgba(40,80,10,.55);
  display:flex;align-items:center;justify-content:space-between;padding:0 22px 0 21px}
.hero-caption span{color:var(--white);font-style:italic;font-weight:600;font-size:26px;letter-spacing:.3px}
.dots{display:flex;gap:5px}
.dots i{width:9px;height:9px;border-radius:50%;background:#e8e8e8;display:block}

.teaser{top:477px;width:195px}
.teaser .frame{height:123px}
.teaser .pic{width:100%;height:100%}
.teaser p{margin:14px 0 0 6px;font-style:italic;font-weight:600;font-size:17px;color:#222}
.t1{left:91px}.t2{left:326px}.t3{left:561px}
.pic-lake{background:linear-gradient(160deg,#7dae52,#9cc5b7 50%,#3f6e2c)}
.pic-path{background:linear-gradient(180deg,#c7d64a,#7d9a2a 55%,#4e6a1a)}
.pic-moon{background:linear-gradient(180deg,#0d1e66,#35529b 45%,#e6a06b 55%,#1d2b5c)}

.welcome{left:91px;top:676px;font-size:27px;font-weight:400;color:var(--ink)}
.copy{left:99px;width:637px;font-size:12.3px;line-height:20px;text-align:justify}
.copy.p1{top:733px}.copy.p2{top:920px}

.widget{left:797px;width:214px;background:var(--panel)}
.widget h3{background:var(--brand);color:var(--white);font-weight:400;font-size:17px;height:42px;line-height:42px;padding-left:20px;border-radius:8px 8px 0 0}
.services{top:477px;height:271px}
.services ul{list-style:none;padding:14px 0 0 13px}
.services li{font-size:12px;color:#333;height:27px;display:flex;align-items:center;gap:9px;white-space:nowrap}
.services li::before{content:"";width:4px;height:4px;background:var(--brand)}
.gallery{top:827px;height:229px}
.thumbs{display:grid;grid-template-columns:repeat(3,53px);gap:8px 8px;padding:10px 0 0 19px}
.thumbs div{height:53px;border-radius:7px}
.g1{background:linear-gradient(#5fb8d8,#e0f2f4)}
.g2{background:linear-gradient(#c9945a,#3b4a55)}
.g3{background:linear-gradient(#2a3a4a,#5a3ad8)}
.g4{background:linear-gradient(#7da8d8,#c43a2a)}
.g5{background:linear-gradient(#4a6b2a,#a8c85a)}
.g6{background:linear-gradient(#1a2aa8,#9ab8e8)}
.more{display:block;margin:25px 0 0 67px;width:92px;height:18px;border-radius:6px;background:var(--button);color:var(--white);font-size:10.5px;text-align:center;line-height:18px}
.shadow-line{height:4px;width:170px;margin:0 auto;background:radial-gradient(ellipse at center,rgba(0,0,0,.12),transparent 70%)}

.footer{left:0;top:1117px;width:1100px;height:83px;background:var(--brand-dark);color:var(--white)}
.footer-links{position:absolute;left:92px;top:17px;font-size:13.5px}
.footer-links span{margin:0 6px}
.footer-copy{position:absolute;left:92px;top:45px;font-size:13.5px}
.social{position:absolute;left:830px;top:22px;display:flex;align-items:center;gap:6px}
.social em{font-family:"Kaushan Script",cursive;font-style:normal;font-size:18px;margin-right:14px}
.social i{width:28px;height:28px;border-radius:5px;background:#4e84c4;border:2px solid #d8e4f4;display:block}
</style>
</head>
<body>
<div class="brand abs"><div class="brand-mark"></div><div class="brand-name">Ruben ter Horst</div></div>

<nav class="nav abs">
  <a class="active">Home</a><a>About Us</a><a>Services</a><a>Why Life Coaching?</a><a>FAQs</a><a>Contact Us</a>
</nav>

<section class="hero frame abs">
  <div class="hero-photo" role="img" aria-label="Panoramic photo of green mountains, a turquoise lake and a grassy meadow with pine trees">
    <div class="hero-caption"><span>Transition life coaching</span><div class="dots"><i></i><i></i><i></i><i></i></div></div>
  </div>
</section>

<div class="teaser t1 abs"><div class="frame"><div class="pic pic-lake" role="img" aria-label="Photo of a bench by a misty lake under trees"></div></div><p>About Us</p></div>
<div class="teaser t2 abs"><div class="frame"><div class="pic pic-path" role="img" aria-label="Photo of a sunlit forest path"></div></div><p>Why Life Coaching</p></div>
<div class="teaser t3 abs"><div class="frame"><div class="pic pic-moon" role="img" aria-label="Photo of a moonlit lake at dusk"></div></div><p>Faqs</p></div>

<h1 class="welcome abs">Welcome to Ruben ter Horst Life Coach</h1>
<p class="copy p1 abs">Maecenas ipsum metus, semper hendrerit varius mattis, congue sit amet tellus. Aliquam ullamcorper dui sed magna posue re ut elementum enim rutrum. Nam mi erat, porta id ultrices nec, pellentesque vel nunc. Cras varius fermentum iaculis. Aenean sodales nibh non lectus tempor a interdum justo ultricies.Maecenas ipsum metus, semper hendrerit varius mattis, congue sit amet tellus. Aliquam ullamcorper dui sed magna posue re ut elementum enim rutrum. Nam mi erat, porta id ultrices nec, pellentesque vel nunc. Cras varius fermentum iaculis. Aenean sodales nibh non lectus tempor a interdum justo ultricies.Maecenas ipsum metus, semper hendrerit varius mattis, congue sit amet tellus. Aliquam ullamcorper dui sed magna posue re ut elementum enim rutrum. Nam mi erat, porta id ultrices nec, pellentesque vel nunc. Cras varius fermentum iaculis. Aenean sodales nibh non lectus tempor a interdum justo ultricies.</p>
<p class="copy p2 abs">Maecenas ipsum metus, semper hendrerit varius mattis, congue sit amet tellus. Aliquam ullamcorper dui sed magna posue re ut elementum enim rutrum. Nam mi erat, porta id ultrices nec, pellentesque vel nunc. Cras varius fermentum iaculis. Aenean sodales nibh non lectus tempor a interdum justo ultricies.Maecenas ipsum metus, semper hendrerit varius mattis, congue sit amet tellus. Aliquam ullamcorper dui sed magna posue re ut elementum enim rutrum. Nam mi erat, porta id ultrices nec, pellentesque vel nunc. Cras varius fermentum iaculis. Aenean sodales nibh non lectus tempor a interdum justo ultricies.Maecenas ipsum metus, semper hendrerit varius mattis, congue sit amet tellus. Aliquam ullamcorper dui sed magna posue re ut elementum enim rutrum. Nam mi erat, porta id ultrices nec, pellentesque vel nunc. Cras varius fermentum iaculis.</p>

<aside class="widget services abs">
  <h3>SERVICES</h3>
  <ul>
    <li>Maecenas ipsum metus</li><li>semper hendrerit varius</li><li>mattis, congue sit amet tellus.</li><li>Aliquam ullamcorper dui sed magna</li><li>posue re ut elementum</li><li>enim rutrum. Nam mi erat,</li><li>porta id ultrices nec, pellentesque</li>
  </ul>
</aside>

<aside class="widget gallery abs">
  <h3>GELLARY</h3>
  <div class="thumbs">
    <div class="g1" role="img" aria-label="Tropical beach photo"></div>
    <div class="g2" role="img" aria-label="Sunset over rocks photo"></div>
    <div class="g3" role="img" aria-label="Evening pool photo"></div>
    <div class="g4" role="img" aria-label="Lake with red flowers photo"></div>
    <div class="g5" role="img" aria-label="Forest photo"></div>
    <div class="g6" role="img" aria-label="Blue night landscape photo"></div>
  </div>
  <span class="more">More Gallery &gt;&gt;</span>
</aside>

<footer class="footer abs">
  <div class="footer-links">Home<span>|</span>About Us<span>|</span>Services<span>|</span>Why Life Coaching?<span>|</span> FAQs <span>|</span> Contact Us</div>
  <div class="footer-copy">Copyright © 2014 Ruben ter Horst Life Coach |&nbsp; All Rights Reserved</div>
  <div class="social"><em>Lets Get Social</em><i></i><i></i></div>
</footer>
</body>
</html>
```